QVR business card

Need a business card for a company that provides instructional design and elearning development services. The website is here: http://quorvane.studio/

I'm attaching a current logo, as well as the old business card design. While I like to keep it clean, the old design is too simplistic for my liking. The only idea I want to reuse from the old design is placing industry jargon on the back of the card, just need a better way to present it. But if you have other ideas for the back--feel free to experiment.

Please use the colors complementary to the color we have on the website. Thank you!

```html
<!DOCTYPE html>
<html lang="en">
<head>
<meta charset="utf-8">
<title>QVR business card</title>
<link rel="stylesheet" href="https://fonts.googleapis.com/css2?family=Montserrat:wght@700&family=Roboto+Condensed:wght@700&family=Fira+Sans:wght@400;500&display=swap">
<style>
  :root {
    --canvas: #aaa8a8;
    --card-dark: #2d2d30;
    --card-light: #f7f7f5;
    --teal: #1cb09b;
    --khaki: #d9d18d;
    --rule: #e6d79e;
    --ink: #2f2f2f;
    --ink-soft: #3d3d3d;
    --white: #ffffff;
  }
  html, body {
    margin: 0;
    padding: 0;
    width: 1200px;
    height: 1200px;
    overflow: hidden;
    background: var(--canvas);
  }
  .canvas {
    position: relative;
    width: 1200px;
    height: 1200px;
  }
  .card-back-terms {
    position: absolute;
    left: 238px;
    top: 118px;
    width: 712px;
    height: 419px;
  }
  .term-line {
    font-family: "Montserrat", sans-serif;
    font-weight: 700;
    font-size: 46px;
    fill: var(--teal);
  }
  .term-question {
    font-family: "Roboto Condensed", sans-serif;
    font-weight: 700;
    font-size: 78px;
    fill: var(--white);
  }
  .card-front {
    position: absolute;
    left: 231px;
    top: 645px;
    width: 711px;
    height: 416px;
    border-radius: 22px;
    background: var(--card-light);
    overflow: hidden;
    font-family: "Fira Sans", sans-serif;
  }
  .brand {
    position: absolute;
    left: 38px;
    top: 44px;
    display: flex;
    align-items: center;
    gap: 14px;
  }
  .brand-dot {
    width: 34px;
    height: 34px;
    border-radius: 50%;
    background: var(--teal);
  }
  .brand-name {
    font-family: "Fira Sans", sans-serif;
    font-weight: 500;
    font-size: 56px;
    letter-spacing: 2px;
    color: var(--teal);
    line-height: 1;
  }
  .holder {
    position: absolute;
    right: 32px;
    top: 196px;
    text-align: right;
  }
  .holder-name {
    font-weight: 500;
    font-size: 20px;
    color: var(--ink);
    letter-spacing: 0.3px;
  }
  .holder-role {
    font-weight: 400;
    font-size: 16px;
    color: var(--ink-soft);
    margin-top: 6px;
  }
  .rule {
    position: absolute;
    left: 37px;
    top: 242px;
    width: 482px;
    height: 1.5px;
    background: var(--rule);
  }
  .contacts {
    position: absolute;
    left: 38px;
    top: 272px;
    margin: 0;
    padding: 0;
    list-style: none;
  }
  .contacts li {
    display: flex;
    align-items: center;
    height: 27px;
    font-size: 17px;
    color: var(--ink);
  }
  .contacts svg {
    width: 16px;
    height: 16px;
    margin-right: 18px;
    fill: var(--teal);
  }
  .footer-band {
    position: absolute;
    left: 0;
    bottom: 0;
    width: 711px;
    height: 44px;
  }
</style>
</head>
<body>
<main class="canvas">

  <svg class="card-back-terms" viewBox="0 0 712 419" aria-label="Card back with studio services">
    <rect x="0" y="0" width="712" height="419" rx="22" fill="var(--card-dark)"/>
    <text class="term-line" x="42" y="60" textLength="630" lengthAdjust="spacingAndGlyphs">MICROLEARNING STORYBOARDS</text>
    <text class="term-line" x="42" y="113" textLength="630" lengthAdjust="spacingAndGlyphs">ASSESSMENT DESIGN VIDEO</text>
    <text class="term-line" x="42" y="166" textLength="630" lengthAdjust="spacingAndGlyphs">ACCESSIBILITY ONBOARDING</text>
    <rect x="0" y="205" width="24" height="35" fill="var(--white)"/>
    <rect x="689" y="205" width="23" height="35" fill="var(--white)"/>
    <text class="term-question" x="42" y="239" textLength="633" lengthAdjust="spacingAndGlyphs">WHAT SHALL WE BUILD?</text>
    <text class="term-line" x="42" y="285" textLength="632" lengthAdjust="spacingAndGlyphs">SIMULATIONS CURRICULUM</text>
    <text class="term-line" x="42" y="339" textLength="632" lengthAdjust="spacingAndGlyphs">PERFORMANCE SUPPORT</text>
    <text class="term-line" x="42" y="392" textLength="634" lengthAdjust="spacingAndGlyphs">CMI5 LEARNING PATHWAYS</text>
  </svg>

  <section class="card-front" aria-label="Card front">
    <div class="brand">
      <span class="brand-dot"></span>
      <span class="brand-name">QVR</span>
    </div>

    <div class="holder">
      <div class="holder-name">Marcus Delvane</div>
      <div class="holder-role">Managing Director</div>
    </div>

    <div class="rule"></div>

    <ul class="contacts">
      <li>
        <svg viewBox="0 0 16 16" aria-hidden="true"><path d="M2 5c0-2 3-3 6-3s6 1 6 3v1h-3V5H5v1H2z"/><rect x="3" y="7" width="10" height="7" rx="1.5"/></svg>
        555-014-2273
      </li>
      <li>
        <svg viewBox="0 0 16 16" aria-hidden="true"><circle cx="8" cy="8" r="7"/><path d="M1 8h14M8 1c-3 3.5-3 10.5 0 14M8 1c3 3.5 3 10.5 0 14" stroke="var(--card-light)" stroke-width="1.2" fill="none"/></svg>
        www.quorvane.studio
      </li>
      <li>
        <svg viewBox="0 0 16 16" aria-hidden="true"><rect x="1" y="3" width="14" height="10" rx="1"/><path d="M1.5 3.5 8 9l6.5-5.5" stroke="var(--card-light)" stroke-width="1.3" fill="none"/></svg>
        mdelvane@quorvane.studio
      </li>
    </ul>

    <svg class="footer-band" viewBox="0 0 711 44" preserveAspectRatio="none" aria-hidden="true">
      <rect x="0" y="22" width="390" height="22" fill="var(--khaki)"/>
      <polygon points="398,0 711,0 711,44 376,44" fill="var(--teal)"/>
    </svg>
  </section>

</main>
</body>
</html>
```